Dunmore Roofing

Want a professional looking business card

Industry/Entity Type

Business

Contact Information for Business Card

Paul Dunmore ( Owner) paul@dunmoreroofing-example.com, www.dunmoreroofing-example.com, Adress: 4172 Township road 43 Alderbrook,WR K9X4T2

```html
<!DOCTYPE html>
<html lang="en">
<head>
<meta charset="utf-8">
<title>Dunmore Roofing – Business Card</title>
<link rel="stylesheet" href="https://fonts.googleapis.com/css2?family=Open+Sans:wght@400;600;700&family=Oswald:wght@600&display=swap">
<style>
  :root {
    --bg: #141414;
    --card-dark: #1c1c1c;
    --card-light: #2e2e2e;
    --brand-blue: #1f4b96;
    --link-blue: #2a59ad;
    --grey-block: #7d7d80;
    --text-white: #f2f2f2;
  }
  * { margin: 0; padding: 0; box-sizing: border-box; }
  html, body {
    width: 1200px; height: 900px; overflow: hidden;
    background: var(--bg);
    font-family: "Open Sans", Arial, sans-serif;
  }
  .canvas {
    position: relative; width: 1200px; height: 900px;
    display: flex; flex-direction: column; align-items: center; justify-content: center;
    gap: 40px;
  }
  .card {
    position: relative; width: 700px; height: 400px;
    background: linear-gradient(135deg, var(--card-dark) 0%, var(--card-dark) 45%, var(--card-light) 100%);
    box-shadow: 0 10px 30px rgba(0,0,0,.6);
    overflow: hidden;
  }
  /* front */
  .card-front { display: flex; flex-direction: column; align-items: center; }
  .brand-lockup {
    margin-top: 155px; display: flex; align-items: center; gap: 14px;
  }
  .brand-square { width: 22px; height: 22px; background: var(--brand-blue); }
  .brand-name {
    font-weight: 700; font-size: 40px; letter-spacing: 2px; line-height: 1;
    color: var(--brand-blue); text-transform: uppercase; white-space: nowrap;
  }
  .front-web {
    position: absolute; bottom: 60px; width: 100%; text-align: center;
    font-size: 15px; letter-spacing: 1px; color: var(--text-white);
  }
  .domain { color: var(--link-blue); }
  /* back */
  .identity {
    position: absolute; left: 50px; top: 135px; width: 300px; text-align: right;
  }
  .person-name {
    font-family: "Oswald", "Arial Narrow", sans-serif; font-weight: 600;
    font-size: 36px; color: var(--brand-blue); text-transform: uppercase;
    line-height: 1.1; white-space: nowrap;
  }
  .person-role { font-size: 21px; color: var(--text-white); line-height: 1.2; }
  .divider {
    position: absolute; left: 368px; top: 132px; width: 2px; height: 80px;
    background: var(--brand-blue);
  }
  .contact-list {
    position: absolute; left: 388px; top: 138px; list-style: none;
    font-size: 14px; letter-spacing: .3px; color: var(--text-white);
    white-space: nowrap;
  }
  .contact-list li { display: flex; align-items: center; gap: 9px; height: 24px; }
  .contact-list svg { width: 14px; height: 14px; flex: none; }
  .address-band {
    position: absolute; left: 0; right: 0; bottom: 40px; height: 38px;
  }
  .band-block { position: absolute; top: 0; height: 38px; background: var(--grey-block); }
  .band-block.left { left: 8px; width: 62px; }
  .band-block.right { left: 612px; width: 62px; }
  .band-main {
    position: absolute; left: 78px; width: 526px; height: 38px;
    background: var(--brand-blue); color: var(--text-white);
    display: flex; align-items: center; justify-content: center; gap: 10px;
    font-size: 16px; letter-spacing: .5px; white-space: nowrap;
  }
  .band-main svg { width: 16px; height: 16px; flex: none; }
</style>
</head>
<body>
<main class="canvas">
  <section class="card card-front" aria-label="Card front">
    <div class="brand-lockup">
      <span class="brand-square"></span>
      <span class="brand-name">Dunmore Roofing</span>
    </div>
    <p class="front-web">www.<span class="domain">dunmoreroofing-example</span>.com</p>
  </section>

  <section class="card card-back" aria-label="Card back">
    <div class="identity">
      <h1 class="person-name">Paul Dunmore</h1>
      <p class="person-role">Owner</p>
    </div>
    <div class="divider"></div>
    <ul class="contact-list">
      <li>
        <svg viewBox="0 0 14 14"><rect x="3.5" y="1" width="7" height="12" rx="1.2" fill="none" stroke="#2a59ad" stroke-width="1.4"/></svg>
        (000)555-0182
      </li>
      <li>
        <svg viewBox="0 0 14 14"><rect x="1" y="3" width="12" height="8" fill="#2a59ad"/><path d="M1 3 L7 8 L13 3" fill="none" stroke="#1c1c1c" stroke-width="1.2"/></svg>
        paul@dunmoreroofing-example.com
      </li>
      <li>
        <svg viewBox="0 0 14 14"><circle cx="6" cy="6" r="4" fill="none" stroke="#2a59ad" stroke-width="1.6"/><path d="M9 9 L13 13" stroke="#2a59ad" stroke-width="1.8"/></svg>
        <span>www.<span class="domain">dunmoreroofing-example</span>.com</span>
      </li>
    </ul>
    <div class="address-band">
      <span class="band-block left"></span>
      <div class="band-main">
        <svg viewBox="0 0 16 16"><path d="M15 1 L1 7 L7 9 L9 15 Z" fill="#f2f2f2"/></svg>
        4172 Township road 43 Alderbrook,WR K9X4T2
      </div>
      <span class="band-block right"></span>
    </div>
  </section>
</main>
</body>
</html>
```